List Now, Launch Later - DL Flyer front & back

Looking for a flyer that has nothing much other than “List Now, Launch Later” on the front with text to fill the back. With image on front that symbolises launch, maybe house being launch like a rocket.
The text has yet to be written but here is the gist: This is for the back of flyer.
List property and delay the launch. In the meantime, we can:
· Prepare contract
· Prepare marketing
· Prepare the property
· Do the Pest and Building Report
· Give the tenants their due notice of sale
· Advise buyers in an off market capacity
This ensures we are first to market when the time comes rather than coming onto the market along with a surge of spring sellers. Buyers are still buying now. The lack of stock is inadvertently creating strength in the market.
The feel has to be modern, clean, contemporary & graphic

```html
<!DOCTYPE html>
<html lang="en">
<head>
<meta charset="utf-8">
<title>List Now, Launch Later</title>
<link href="https://fonts.googleapis.com/css2?family=Montserrat:wght@700&display=swap" rel="stylesheet">
<style>
  :root {
    --ink: #050505;
    --white: #ffffff;
    --accent: #fbb040;
    --photo-top: #2c2c2c;
    --photo-mid: #3b3b3b;
    --photo-floor: #6b5442;
    --shade: rgba(0, 0, 0, 0.82);
  }
  html, body {
    margin: 0;
    padding: 0;
    overflow: hidden;
    background: #ffffff;
  }
  .flyer {
    position: relative;
    width: 848px;
    height: 1200px;
    overflow: hidden;
    font-family: "Montserrat", sans-serif;
  }
  .room-photo {
    position: absolute;
    inset: 0;
    background:
      linear-gradient(90deg, rgba(200,200,200,0.35) 0%, rgba(200,200,200,0.15) 8%, rgba(0,0,0,0) 12%),
      linear-gradient(180deg, var(--photo-top) 0%, var(--photo-mid) 60%, var(--photo-floor) 80%, #4a3a2e 100%);
  }
  .shade-panel {
    position: absolute;
    left: 73px;
    top: 0;
    right: 0;
    height: 1091px;
    background: var(--shade);
  }
  .rocket-house {
    position: absolute;
    left: 190px;
    top: 172px;
    width: 276px;
    height: 322px;
    border-radius: 60px;
    background: radial-gradient(circle at 60% 40%, rgba(235,235,235,0.55), rgba(235,235,235,0.15) 60%, rgba(251,176,64,0.25) 100%);
  }
  .rule {
    position: absolute;
    left: 190px;
    top: 699px;
    width: 168px;
    height: 4px;
    background: var(--white);
  }
  .headline-band {
    position: absolute;
    left: 142px;
    top: 897px;
    right: 0;
    height: 80px;
    background: var(--ink);
  }
  .headline {
    position: absolute;
    left: 186px;
    top: 757px;
    margin: 0;
    color: var(--white);
    font-weight: 700;
    font-size: 69px;
    line-height: 76.5px;
    letter-spacing: -0.5px;
    text-transform: uppercase;
  }
  .next-arrow {
    position: absolute;
    left: 758px;
    top: 910px;
  }
</style>
</head>
<body>
  <div class="flyer">
    <div class="room-photo" role="img" aria-label="Dim modern living room with white sofa, coffee table, fireplace and timber floor"></div>
    <div class="shade-panel"></div>
    <div class="rocket-house" role="img" aria-label="Illustration of a house shape launching like a rocket with an orange flame"></div>
    <div class="rule"></div>
    <div class="headline-band"></div>
    <h1 class="headline">List now,<br>launch<br>later.</h1>
    <svg class="next-arrow" width="34" height="63" viewBox="0 0 34 63" aria-hidden="true">
      <polygon points="0,0 34,31.5 0,63" fill="var(--accent)"/>
    </svg>
  </div>
</body>
</html>
```